Probate (Legal) Wordpress Design with Coding for Online Company

I need a Wordpress design with coding, pictures, content to be provided by me, fully responsive, and development. This is for a 6-7 page design.

Pages Needed: Home/About/Probate/Process/FAQ/Contact Us/Blog.

The home page should be organized as followed:
-Steps in Probate: Gather; Implement; Close (each step will come with content)
-Flat-Fee Price & Savings: Content will go here with a button to contact us (phone number) or just the phone number.
-You Have Questions, We Have Answers: five questions with content. Only one question answer to show at a time when clicked on the question from the list.
-Get to Know Us: a brief description with content about what we do and who we are.

Main image slogan: Helping Californians deal with loss with DIGNITY & UNDERSTATING (you may use a better slogan if you wish).

The Contact page should not have a map since we are an online company. We service the entire state of California in every county and city.

The About page should be simple, direct, and easy on the eye. It should have a brief description of who we are and it should have no more than 6 reasons why the client should hire us.

About our online California company. We are not attorneys but legal document assistants who prepare legal documents for probate estate when someone dies with or without a will and assets need to be distributed. We have a flat-fee for Formal Probate of $999 and $699 for Informal Probate. We are an online company and offer our services to the entire state of California in every county. We do everything over the phone and email. The turn around time for us to prepare the initial legal paperwork for the client is within 3-5 business days. We can prepare, file, serve and manage a probate matter from petition to closing. We are not attorneys so our prices are very affordable compare to the attorney.

The company name for the website will be www.velmarhollow.com, The Velmar Hollow Group.

I do not have a logo yet. The colors of the website should be easy on the eye and calming. THE SITE SHOULD BE SIMPLE AND STRAIGHT TO THE POINT. EASY TO NAVIGATE.

The company phone number should be very visible and should stand out to the client. It should also be clickable and ready to dial for smartphone users.

I do not want a contact form on the homepage. THE MAIN THING IS FOR THE POTENTIAL CLIENT TO CALL OUR OFFICE TO SIGN UP.

I do like some images of family or people since we are dealing with people who just lost a loved one. Not all the images have to be of people.

The site should not look like we practice law or that people can mistake us for attorneys.

Target Market(s)

People who just lost a loved one who had property, assets, in California but died with or without a will or trust. This is for people looking to hire non-attorneys.

Coding

Coded - Design and coding required

Font styles to use
Serif

Colors

Designer to choose colors to be used in the design.

Requirements
Must have
• Refer to Project Description.
Nice to have
• The sample images provided is what I am attracted to for the homepage image.
Should not have

```html
<!DOCTYPE html>
<html lang="en">
<head>
<meta charset="utf-8">
<title>Contact Us – The Velmar Hollow Group</title>
<link href="https://fonts.googleapis.com/css2?family=EB+Garamond:wght@500;600;700&family=Open+Sans:wght@400;600&display=swap" rel="stylesheet">
<style>
:root{
  --orange:#f7870f;
  --teal:#137c94;
  --ink:#222;
  --body:#444;
  --line:#1a1a1a;
  --white:#fff;
  --photo-warm:#cdbfae;
  --photo-soft:#e6ddd2;
}
*{margin:0;padding:0;box-sizing:border-box}
html,body{width:884px;height:1200px;overflow:hidden;background:var(--white)}
body{position:relative;font-family:"Open Sans",sans-serif;color:var(--ink)}
.site-header{position:absolute;top:0;left:0;width:884px;height:92px;border-top:2px solid var(--orange)}
.brand{position:absolute;left:73px;top:34px;width:160px;font-family:"EB Garamond",serif;font-weight:700;font-size:17px;line-height:19px;color:var(--teal);letter-spacing:.5px;text-transform:uppercase}
.call-pill{position:absolute;left:584px;top:0;width:216px;height:32px;background:var(--orange);border-radius:0 0 22px 22px;color:var(--white);font-weight:600;font-size:12.5px;display:flex;align-items:center;justify-content:center;gap:8px}
.main-nav{position:absolute;top:57px;left:337px;width:474px;display:flex;justify-content:space-between;font-size:11.2px;font-weight:600;color:var(--ink)}
.hero{position:absolute;top:92px;left:0;width:884px;height:142px;background:linear-gradient(90deg,#5b5b5b 0%,#6c6864 45%,#8a7a6a 70%,#6a5d52 100%)}
.hero-title{position:absolute;left:73px;top:50px;font-family:"EB Garamond",serif;font-weight:600;font-size:41px;color:var(--white);letter-spacing:.5px}
.contact-photo{position:absolute;left:73px;top:296px;width:362px;height:269px;border-radius:3px;background:linear-gradient(135deg,var(--photo-soft) 0%,var(--photo-warm) 100%)}
.contact-block{position:absolute;left:466px;top:318px;width:345px}
.section-heading{font-family:"EB Garamond",serif;font-weight:600;font-size:26px;color:var(--teal);letter-spacing:.3px}
.rule{width:68px;height:2px;background:var(--teal);margin-top:10px}
.contact-block p{margin-top:22px;font-size:11.2px;line-height:19px;color:var(--body);text-align:justify}
.contact-line{display:flex;align-items:center;gap:10px;font-size:15px;color:var(--ink)}
.contact-block .contact-line{margin-top:22px}
.contact-block .contact-line + .contact-line{margin-top:18px}
.icon{width:33px;height:33px;flex:none}
.info-band{position:absolute;top:621px;left:0;width:884px;height:359px;display:flex}
.info-panel{width:442px;height:359px;padding:46px 0 0 73px;color:var(--white)}
.info-panel.what{background:linear-gradient(135deg,#2a9cb8,#137f9c)}
.info-panel.who{padding-left:24px;background:linear-gradient(135deg,#c07a22,#a9661a)}
.info-panel h2{font-family:"EB Garamond",serif;font-weight:600;font-size:25px;letter-spacing:.5px}
.info-panel .rule{width:80px;background:var(--white);margin-top:10px}
.info-panel p{width:350px;font-size:10.3px;line-height:17.6px;font-weight:600;margin-top:26px}
.info-panel p + p{margin-top:16px}
.btn{display:inline-block;margin-top:26px;border:1.5px solid var(--white);padding:10px 8px;font-size:12px;font-weight:600;color:var(--white)}
.site-footer{position:absolute;top:1030px;left:0;width:884px}
.footer-nav{display:flex;justify-content:center;gap:22px;font-size:11.2px;font-weight:600;color:var(--ink)}
.footer-nav .sep{font-weight:400;color:var(--ink)}
.footer-contact{display:flex;justify-content:center;gap:32px;margin-top:34px}
.footer-rule{width:738px;height:2px;background:var(--line);margin:22px auto 0}
.copyright{text-align:center;font-size:11.2px;color:var(--ink);margin-top:18px}
</style>
</head>
<body>
<header class="site-header">
  <div class="brand">The Velmar Hollow Group</div>
  <div class="call-pill">
    <svg width="12" height="12" viewBox="0 0 12 12"><rect width="12" height="12" rx="2" fill="#fff"/><path d="M3.4 2.6l1.4 0 .6 1.8-.9.7a4.5 4.5 0 0 0 2.4 2.4l.7-.9 1.8.6v1.4c0 .4-.4.7-.8.7A6 6 0 0 1 2.7 3.4c0-.4.3-.8.7-.8z" fill="#f7870f"/></svg>
    Call Us At: +180 555 0147
  </div>
  <nav class="main-nav"><span>HOME</span><span>ABOUT</span><span>PROBATE</span><span>PROCESS</span><span>FAQ</span><span>CONTACT US</span><span>BLOG</span></nav>
</header>

<section class="hero" role="img" aria-label="Photo of two young children embracing">
  <h1 class="hero-title">CONTACT US</h1>
</section>

<div class="contact-photo" role="img" aria-label="Photo of a family together at home"></div>

<section class="contact-block">
  <h2 class="section-heading">CONTACT US</h2>
  <div class="rule"></div>
  <p>Nemo enim ipsam voluptatem quia voluptas sit aspernatur aut odit aut fugit, sed quia consequuntur magni dolores.</p>
  <div class="contact-line">
    <svg class="icon" viewBox="0 0 33 33"><circle cx="16.5" cy="16.5" r="15.5" fill="none" stroke="#222" stroke-width="1.5"/><path d="M12 10h2.5l1.2 3.2-1.6 1.2a8 8 0 0 0 4.5 4.5l1.2-1.6 3.2 1.2V21c0 .8-.7 1.4-1.5 1.4A11 11 0 0 1 10.6 11.5c0-.8.6-1.5 1.4-1.5z" fill="#222"/></svg>
    +180 555 0147
  </div>
  <div class="contact-line">
    <svg class="icon" viewBox="0 0 33 33"><circle cx="16.5" cy="16.5" r="15.5" fill="none" stroke="#222" stroke-width="1.5"/><rect x="10" y="11.5" width="13" height="10" rx="1.5" fill="none" stroke="#222" stroke-width="1.5"/><path d="M10.5 12.5l6 5 6-5" fill="none" stroke="#222" stroke-width="1.5"/></svg>
    info@velmarhollow.com
  </div>
</section>

<section class="info-band">
  <div class="info-panel what" role="img" aria-label="Photo of hands over paperwork, tinted blue">
    <h2>WHAT WE DO</h2>
    <div class="rule"></div>
    <p>Sed ut perspiciatis unde omnis iste natus error sit voluptatem accu santium doloremque laudantium, totam rem aperiam, eaque ipsa quae ab illo inventore veritatis et quasi architecto beatae.</p>
    <p>Nemo enim ipsam voluptatem quia voluptas sit aspernatur aut odit aut fugit, sed quia consequuntur magni dolores eos qui ratione vo luptatem.</p>
    <span class="btn">READ MORE</span>
  </div>
  <div class="info-panel who" role="img" aria-label="Photo of a hand signing a document, tinted amber">
    <h2>WHO WE ARE</h2>
    <div class="rule"></div>
    <p>Sed ut perspiciatis unde omnis iste natus error sit voluptatem accu santium doloremque laudantium, totam rem aperiam, eaque ipsa quae ab illo inventore veritatis et quasi architecto beatae.</p>
    <p>Nemo enim ipsam voluptatem quia voluptas sit aspernatur aut odit aut fugit, sed quia consequuntur magni dolores eos qui ratione vo luptatem.</p>
    <span class="btn">READ MORE</span>
  </div>
</section>

<footer class="site-footer">
  <nav class="footer-nav"><span>HOME</span><span class="sep">|</span><span>ABOUT</span><span class="sep">|</span><span>PROBATE</span><span class="sep">|</span><span>PROCESS</span><span class="sep">|</span><span>FAQ</span><span class="sep">|</span><span>CONTACT US</span><span class="sep">|</span><span>BLOG</span></nav>
  <div class="footer-contact">
    <div class="contact-line">
      <svg class="icon" viewBox="0 0 33 33"><circle cx="16.5" cy="16.5" r="15.5" fill="none" stroke="#222" stroke-width="1.5"/><path d="M12 10h2.5l1.2 3.2-1.6 1.2a8 8 0 0 0 4.5 4.5l1.2-1.6 3.2 1.2V21c0 .8-.7 1.4-1.5 1.4A11 11 0 0 1 10.6 11.5c0-.8.6-1.5 1.4-1.5z" fill="#222"/></svg>
      +180 555 0147
    </div>
    <div class="contact-line">
      <svg class="icon" viewBox="0 0 33 33"><circle cx="16.5" cy="16.5" r="15.5" fill="none" stroke="#222" stroke-width="1.5"/><rect x="10" y="11.5" width="13" height="10" rx="1.5" fill="none" stroke="#222" stroke-width="1.5"/><path d="M10.5 12.5l6 5 6-5" fill="none" stroke="#222" stroke-width="1.5"/></svg>
      info@velmarhollow.com
    </div>
  </div>
  <div class="footer-rule"></div>
  <p class="copyright">Copyrights @ 2017 The Velmar Hollow Group. All Rights Reserved.</p>
</footer>
</body>
</html>
```